Postcard Design

We are an upscale, full service real estate boutique based in Mt. Pleasant, SC. We will be having a Grand Opening of our beautiful, new office complete with high end custom home architecture and design. I will attach photos for your review. I would like to come up with a medium postcard to be mailed to clientele of Mt. Pleasant. Home prices between $300,000 - $2.2 million. The customers can call our office for the Grand Opening Listing Promotion or stop by our grand opening. We will have drawings for door prizes that include services at Brisklane Day Spa, Tangy Pepperpot gift certificates, and they can register to win a cruise with a listing presentation. Our Grand Opening will be a couple of different dates, April 7, 2016 and April 21, 2016. I will want an order that lists the 7th and another order that will list the 21. The look should have a very "relaxing, beach" feel, but not Myrtle Beach...should reflect colors of the ocean, like you are on vacation. I will include logos and pics for your review. Thank you!

```html
<!DOCTYPE html>
<html lang="en">
<head>
<meta charset="utf-8">
<title>Grand Opening Postcard – Seagrove Real Estate</title>
<link rel="stylesheet" href="https://fonts.googleapis.com/css2?family=Lobster&family=Open+Sans:wght@400;600;700&display=swap">
<style>
  :root {
    --page-bg: #e8ebee;
    --card-bg: #ffffff;
    --sky-band: #7ccff3;
    --sea-light: #c4e9fa;
    --brand-blue: #1a8fd0;
    --deep-blue: #1e5fa8;
    --date-blue: #2a73b8;
    --bar-dark: #0d5d9f;
    --bar-light: #1b93d6;
    --text-grey: #555a5f;
    --muted-grey: #8a8d90;
    --rule-grey: #cfd3d6;
    --photo-top: #d3e6f4;
    --photo-mid: #aac6e0;
    --photo-low: #92b0cb;
    --photo-base: #8fa27e;
  }
  * { box-sizing: border-box; margin: 0; padding: 0; }
  html, body { width: 940px; height: 1200px; overflow: hidden; }
  body {
    position: relative;
    background: var(--page-bg);
    font-family: "Open Sans", Arial, sans-serif;
  }
  .postcard {
    position: absolute;
    width: 648px;
    height: 500px;
    background: var(--card-bg);
    box-shadow: 0 4px 14px rgba(0,0,0,0.18);
    overflow: hidden;
  }
  .postcard--front { left: 112px; top: 80px; }
  .postcard--back { left: 214px; top: 624px; }
  .front-art { position: absolute; inset: 0; }
  .front-title { font-family: "Lobster", cursive; font-size: 36px; fill: #ffffff; }
  .front-date { font-size: 23px; fill: var(--date-blue); }
  .brand-name { font-size: 17px; font-weight: 700; fill: var(--brand-blue); }
  .front-address { font-size: 13px; fill: var(--muted-grey); }

  .office-snapshot {
    position: absolute;
    left: 28px; top: 32px;
    width: 240px; height: 178px;
    padding: 8px;
    background: #fff;
    transform: rotate(-4deg);
    box-shadow: 0 6px 12px rgba(0,0,0,0.28);
  }
  .office-snapshot__photo {
    width: 100%; height: 100%;
    background: linear-gradient(180deg, var(--photo-top) 0%, var(--photo-mid) 40%, var(--photo-low) 75%, var(--photo-base) 100%);
  }
  .back-title {
    position: absolute; left: 0; width: 353px; top: 210px;
    text-align: center;
    font-family: "Lobster", cursive; font-size: 35px; font-weight: 400; color: var(--deep-blue);
  }
  .back-date {
    position: absolute; left: 0; width: 353px; top: 256px;
    text-align: center; font-size: 21px; color: var(--text-grey);
  }
  .phone-bar {
    position: absolute; left: 0; top: 318px;
    width: 353px; height: 53px;
    background: linear-gradient(90deg, var(--bar-dark), var(--bar-light));
    box-shadow: 0 8px 10px -6px rgba(0,0,0,0.45);
    display: flex; align-items: center; justify-content: center; gap: 10px;
    color: #fff; font-size: 19px;
  }
  .phone-bar svg { width: 15px; height: 15px; fill: #fff; }
  .web-address {
    position: absolute; left: 39px; top: 378px;
    font-size: 19px; color: #1a6fc0;
  }
  .mail-address {
    position: absolute; left: 346px; top: 36px;
    font-size: 16px; line-height: 20px; color: #222; font-style: normal;
  }
  .stamp-box {
    position: absolute; left: 544px; top: 23px;
    width: 89px; height: 71px;
    border: 2px solid var(--rule-grey);
  }
  .address-lines {
    position: absolute; left: 391px; top: 186px; width: 237px;
    list-style: none;
  }
  .address-lines li {
    height: 36px;
    border-top: 2px solid var(--rule-grey);
  }
</style>
</head>
<body>

<section class="postcard postcard--front" aria-label="Postcard front">
  <svg class="front-art" viewBox="0 0 648 500" width="648" height="500">
    <defs>
      <linearGradient id="officeTones" x1="0" y1="0" x2="0" y2="1">
        <stop offset="0" stop-color="var(--photo-top)"/>
        <stop offset="0.4" stop-color="var(--photo-mid)"/>
        <stop offset="0.78" stop-color="var(--photo-low)"/>
        <stop offset="1" stop-color="var(--photo-base)"/>
      </linearGradient>
    </defs>
    <path d="M0,24 C200,6 430,30 648,52 L648,64 C400,40 190,38 0,66 Z" fill="var(--sky-band)"/>
    <path role="img" aria-label="Photo of the new light blue clapboard office building with trees and landscaping"
          d="M0,66 C190,38 400,40 648,64 L648,372 C470,392 260,376 0,362 Z" fill="url(#officeTones)"/>
    <path d="M260,398 C400,384 520,378 648,374 L648,404 C540,420 430,426 330,420 C300,418 280,410 260,398 Z" fill="var(--sea-light)"/>
    <text class="front-title" x="64" y="48">Grand Opening</text>
    <text class="front-date" x="394" y="413">April 7, 2016</text>
    <circle cx="58" cy="452" r="16" fill="var(--brand-blue)"/>
    <text class="brand-name" x="84" y="458">Seagrove Real Estate</text>
    <text class="front-address" x="612" y="472" text-anchor="end">1820 Harbor Road North Mount Pleasant, SC 29464</text>
  </svg>
</section>

<section class="postcard postcard--back" aria-label="Postcard back">
  <figure class="office-snapshot">
    <div class="office-snapshot__photo" role="img" aria-label="Photo of the new office building among trees"></div>
  </figure>
  <h1 class="back-title">Grand Opening</h1>
  <p class="back-date">April 7, 2016</p>
  <div class="phone-bar">
    <svg viewBox="0 0 24 24" aria-hidden="true"><path d="M6.6 10.8a15.1 15.1 0 0 0 6.6 6.6l2.2-2.2a1 1 0 0 1 1-.25 11.4 11.4 0 0 0 3.6.57 1 1 0 0 1 1 1V20a1 1 0 0 1-1 1A17 17 0 0 1 3 4a1 1 0 0 1 1-1h3.5a1 1 0 0 1 1 1c0 1.25.2 2.45.57 3.57a1 1 0 0 1-.25 1z"/></svg>
    <span>843-555-0142</span>
  </div>
  <p class="web-address">www.seagroverealestate.com</p>
  <address class="mail-address">1820 Harbor Road<br>North Mount Pleasant,<br>SC 29464</address>
  <div class="stamp-box" aria-label="Stamp area"></div>
  <ul class="address-lines" aria-label="Recipient address lines">
    <li></li><li></li><li></li><li></li><li></li>
  </ul>
</section>

</body>
</html>
```